Veranix - Solution provider in business consulting

Veranix is a swiss based company providing solutions for developing markets. The business covers various fields of business consulting, such as supply chain, product costs, quality management and manufacturing management. The Business operates in a efficient, straight and solution oriented manner.
The final design should communicate these characteristics. Asian people as well as as western people shall identify the qualities of the company at first sight.
The customer needs business cards with a simple view but an recognizable design, printed in high quality. Engraved elements such as the globe or simple words are possible.
Available colors are: (RAL)
102/102/102
51/102/102
153/204/153
255/102/51
Font: Calibri

```html
<!DOCTYPE html>
<html lang="en">
<head>
<meta charset="utf-8">
<title>Veranix – Business Card</title>
<link href="https://fonts.googleapis.com/css2?family=Carlito:wght@400;700&display=swap" rel="stylesheet">
<style>
  :root {
    --bg-top: #c3c3c3;
    --bg-bottom: #acacac;
    --card-front: #ffffff;
    --card-back: #666666;
    --ink: #666666;
    --ink-strong: #4a4a4a;
    --back-mark: #585858;
  }
  * { margin: 0; padding: 0; box-sizing: border-box; }
  html, body { width: 1200px; height: 900px; overflow: hidden; }
  body {
    background: linear-gradient(180deg, var(--bg-top), var(--bg-bottom));
    font-family: "Carlito", "Calibri", sans-serif;
    color: var(--ink);
    position: relative;
  }
  .card {
    position: absolute;
    top: 306px;
    width: 439px;
    height: 271px;
    border-radius: 10px;
  }
  .card--front { left: 149px; background: var(--card-front); }
  .card--back { left: 608px; background: var(--card-back); }

  .wordmark {
    position: absolute;
    display: flex;
    align-items: center;
    gap: 10px;
    font-weight: 400;
    letter-spacing: 0.5px;
  }
  .card--front .wordmark {
    left: 34px; top: 112px;
    font-size: 42px; color: var(--ink);
  }
  .card--back .wordmark {
    left: 0; right: 0; top: 104px;
    justify-content: center;
    font-size: 54px; color: var(--back-mark);
  }
  .wordmark__dot {
    width: 14px; height: 14px; border-radius: 50%;
    background: currentColor;
  }
  .card--back .wordmark__dot { width: 18px; height: 18px; }

  .details {
    position: absolute;
    left: 247px; top: 50px;
    font-size: 13.5px; line-height: 17px;
  }
  .details__name { font-size: 18px; font-weight: 700; color: var(--ink-strong); line-height: 20px; }
  .details__role { margin-bottom: 13px; }
  .details__address { margin-bottom: 14px; }
  .contact { list-style: none; }
  .contact li { display: flex; align-items: center; height: 18px; }
  .contact svg { width: 10px; height: 10px; margin: 0 7px 0 0; fill: var(--ink); flex: none; }
</style>
</head>
<body>
  <section class="card card--front">
    <div class="wordmark"><span>Veranix</span><span class="wordmark__dot"></span></div>
    <div class="details">
      <p class="details__name">Marco Lenz</p>
      <p class="details__role">CEO</p>
      <p class="details__address">Veranix GmbH Lindenweg 14<br>8412 Talbach Switzerland</p>
      <ul class="contact">
        <li><svg viewBox="0 0 10 10"><path d="M2.5 0h5a1 1 0 0 1 1 1v8a1 1 0 0 1-1 1h-5a1 1 0 0 1-1-1V1a1 1 0 0 1 1-1zm.3 1.2v6.4h4.4V1.2zM5 8.2a.5.5 0 1 0 0 1 .5.5 0 0 0 0-1z"/></svg>+41 79 532 8841</li>
        <li><svg viewBox="0 0 10 10"><path d="M2 0.5 3.6 2.6 2.7 3.7c.6 1.4 2.2 3 3.6 3.6l1.1-.9L9.5 8 8.4 9.5C4.5 9.3.7 5.5.5 1.6z"/></svg>+41 71 864 3307</li>
        <li><svg viewBox="0 0 10 10"><path d="M0 2h10v.6L5 5.6 0 2.6zM0 3.6l5 3 5-3V8H0z"/></svg>marco.lenz@veranix.ch</li>
        <li><svg viewBox="0 0 10 10"><path d="M5 0a5 5 0 1 0 0 10A5 5 0 0 0 5 0zm3.9 4.4H7.2a7 7 0 0 0-.8-3.1 4 4 0 0 1 2.5 3.1zM5 1c.6.8 1 2 1.1 3.4H3.9C4 3 4.4 1.8 5 1zM3.6 1.3a7 7 0 0 0-.8 3.1H1.1a4 4 0 0 1 2.5-3.1zM1.1 5.6h1.7a7 7 0 0 0 .8 3.1 4 4 0 0 1-2.5-3.1zM5 9c-.6-.8-1-2-1.1-3.4h2.2C6 7 5.6 8.2 5 9zm1.4-.3a7 7 0 0 0 .8-3.1h1.7a4 4 0 0 1-2.5 3.1z"/></svg>www.veranix.ch</li>
      </ul>
    </div>
  </section>

  <section class="card card--back">
    <div class="wordmark"><span>Veranix</span><span class="wordmark__dot"></span></div>
  </section>
</body>
</html>
```